Corvane Business Cards

Front of business card will have logo, name, address, & telephone number. Back of card will have a list of services provided - Roads, Substation Pads, Temporary Pads, Site Pads, Land Leveling, Powerline Row Cleaning, Land Clearing, Gates, Fencing, Construction Entrances, Excavation, Trenching, Underground Utilities, Directional Boring, Pile Driving. We are a construction company that uses heavy equipment like bulldozers, motor graders/blades, dump trucks, backhoes, hydro axes, & skid loaders. We build roads, pads, & install electric utility lines & waterlines underground. This logo is new. The word "Construction" can be smaller as uploaded 2 example edited logos. We will be using this card design for many employees.
Target Market(s)
Industrial Electric Powerline, Wind Turbine, Solar Panel, & Water Utility companies.
Contact Information for Business Card
Name/Position - Dwayne Halster - Owner
Address: 4875 FM 309
Merkel, TX 79412
Phone number - (325) 482-5096

```html
<!DOCTYPE html>
<html lang="en">
<head>
<meta charset="utf-8">
<title>Corvane Construction Business Cards</title>
<link rel="stylesheet" href="https://fonts.googleapis.com/css2?family=Montserrat:wght@400;500;600;700&display=swap">
<style>
  :root {
    --backdrop: #3a3a3a;
    --card: #3e111c;
    --card-edge: #4a1a26;
    --ink: #ffffff;
    --ink-soft: rgba(255,255,255,0.85);
  }
  * { margin: 0; padding: 0; box-sizing: border-box; }
  html, body {
    width: 1200px; height: 900px; overflow: hidden;
    background: var(--backdrop);
    font-family: "Montserrat", Arial, sans-serif;
    color: var(--ink);
  }
  .stage {
    position: relative; width: 1200px; height: 900px;
    display: flex; align-items: center; justify-content: center; gap: 30px;
  }
  .card {
    position: relative; width: 555px; height: 317px;
    background: linear-gradient(120deg, var(--card-edge) 0%, var(--card) 35%, var(--card) 100%);
    box-shadow: 0 10px 28px rgba(0,0,0,0.45);
    display: flex; flex-direction: column; align-items: center;
  }
  /* services side */
  .card--services { justify-content: center; }
  .brand-name {
    font-family: "Montserrat", Arial, sans-serif;
    font-weight: 700; letter-spacing: 3px; color: var(--ink);
  }
  .card--services .brand-name { font-size: 46px; margin-bottom: 38px; }
  .services { list-style: none; text-align: center; }
  .services li {
    font-size: 11.5px; font-weight: 500; line-height: 1.65;
    white-space: nowrap; color: var(--ink);
  }
  /* contact side */
  .card--contact { padding-top: 62px; }
  .brand-block { text-align: center; }
  .card--contact .brand-name { font-size: 38px; line-height: 1.1; }
  .card--contact .brand-name--sub { font-size: 24px; letter-spacing: 4px; }
  .contact-row {
    margin-top: 44px; display: flex; align-items: center;
  }
  .person { text-align: right; padding-right: 16px; }
  .person__name { font-size: 17px; font-weight: 700; letter-spacing: 0.5px; }
  .person__role { font-size: 14px; font-weight: 400; }
  .divider { width: 1px; height: 52px; background: var(--ink-soft); }
  .details { padding-left: 16px; list-style: none; }
  .details li {
    display: flex; align-items: center; gap: 8px;
    font-size: 14px; font-weight: 500; line-height: 1.75;
  }
  .details svg { width: 12px; height: 12px; fill: var(--ink); flex: none; }
</style>
</head>
<body>
<main class="stage">
  <section class="card card--services" aria-label="Card back: services">
    <div class="brand-name">CORVANE</div>
    <ul class="services">
      <li>Roads | Substation Pads | Temporary Pads | Site Pads | Land Leveling</li>
      <li>Land Clearing | Gates | Fencing | Construction Entrances | Excavation | Trenching</li>
      <li>Underground Utilities | Powerline Row Cleaning | Pile Driving | Directional Boring</li>
    </ul>
  </section>

  <section class="card card--contact" aria-label="Card front: contact">
    <div class="brand-block">
      <div class="brand-name">CORVANE</div>
      <div class="brand-name brand-name--sub">CONSTRUCTION</div>
    </div>
    <div class="contact-row">
      <div class="person">
        <div class="person__name">DWAYNE HALSTER</div>
        <div class="person__role">Owner</div>
      </div>
      <div class="divider"></div>
      <ul class="details">
        <li>
          <svg viewBox="0 0 24 24" aria-hidden="true"><path d="M6.6 10.8a15.1 15.1 0 0 0 6.6 6.6l2.2-2.2c.3-.3.7-.4 1-.2 1.1.4 2.3.6 3.6.6.6 0 1 .4 1 1V20c0 .6-.4 1-1 1C10.6 21 3 13.4 3 4c0-.6.4-1 1-1h3.5c.6 0 1 .4 1 1 0 1.3.2 2.5.6 3.6.1.3 0 .7-.2 1z"/></svg>
          (325) 482-5096
        </li>
        <li>
          <svg viewBox="0 0 24 24" aria-hidden="true"><path d="M12 2a7 7 0 0 0-7 7c0 5.2 7 13 7 13s7-7.8 7-13a7 7 0 0 0-7-7zm0 9.5A2.5 2.5 0 1 1 12 6.5a2.5 2.5 0 0 1 0 5z"/></svg>
          4875 FM 309 Merkel, TX 79412
        </li>
      </ul>
    </div>
  </section>
</main>
</body>
</html>
```